Mission Statement Board for front lobby

We need a mission statement board for our front lobby at our company called TrellisWorks. We are a web content management company that builds websites for our clients. We would like two boards, same size, canvas material (not thin poster board or anything like that) size H 3' x L 2', white background, blue and black colored font, our logo on top in blue/gray/black and some blue coloring around top and bottom, kind of framing the white background. Please reference our very rough draft we did in Word so you get an idea of what we're thinking- the attachment shows what we would like on each board. Reference our website to see logo and fonts if you would like, please keep the board similar to our fonts and colors. www.trellisworks-example.com

Contact info: Marta Kowalczyk
Email: marta.kowalczyk@trellisworks-example.com
Phone: 555-207-3948
Updates

Please do not include in a design my contact info, no email marta.kowalczyk@trellisworks-example.com, no phone # 555-207-3948. I added that info to the project when I posted it, but it is not part of the design.... reference attachment posted in project with exactly what we want.

Target Market(s)

Clients & employees in the office who will see the boards in lobby

Industry/Entity Type

It Company

Font styles to use
Other font styles liked:
• reference attachment (but font is flexible within reason)

Colors
33a6d7
0255a3
eaf1f7
0292cd
85cae6
cee9f5
000000
5c5c5c
959595

Requirements
Must have
• Needs to be a professional sign that hangs on wall, company logo, cohesive colors and fonts
Nice to have
• Get creative with the border/framing around the white background
Should not have
• Unprofessional fonts, typos, thin cheap looking poster board materal.

```html
<!DOCTYPE html>
<html lang="en">
<head>
<meta charset="utf-8">
<title>TrellisWorks – Our Core Values</title>
<link href="https://fonts.googleapis.com/css2?family=Lato:wght@400;700&display=swap" rel="stylesheet">
<style>
  :root {
    --backdrop: #5a5a5c;
    --navy: #1f3f8f;
    --royal: #2156a8;
    --sky: #33a6d7;
    --sky-light: #85cae6;
    --sky-pale: #cee9f5;
    --mist: #eaf1f7;
    --heading-blue: #1f73b8;
    --ink: #1a1a1a;
    --grey: #5c5c5c;
    --silver: #959595;
  }
  html, body {
    margin: 0;
    width: 843px;
    height: 1200px;
    overflow: hidden;
    background: var(--backdrop);
  }
  .board {
    position: absolute;
    left: 76px;
    top: 82px;
    width: 691px;
    height: 1037px;
    overflow: hidden;
    background: #fff;
    font-family: 'Lato', sans-serif;
    color: var(--ink);
  }
  .board-frame {
    position: absolute;
    inset: 0;
    width: 100%;
    height: 100%;
  }
  .brand {
    position: absolute;
    left: 400px;
    top: 262px;
    width: 270px;
    text-align: center;
  }
  .brand-name {
    font-weight: 700;
    font-size: 32px;
    color: var(--royal);
    line-height: 1;
  }
  .values {
    position: absolute;
    left: 74px;
    top: 373px;
    width: 545px;
  }
  .values-title {
    margin: 0 0 6px;
    font-weight: 700;
    font-size: 34px;
    line-height: 1.1;
    color: var(--heading-blue);
    letter-spacing: -0.5px;
  }
  .value {
    margin: 0 0 27px;
    font-size: 19.5px;
    line-height: 24.5px;
    letter-spacing: 0.2px;
    text-align: justify;
  }
  .value-name {
    font-weight: 700;
    font-size: 22px;
    letter-spacing: 0;
  }
  .value-name.plain {
    font-weight: 400;
    font-size: 19.5px;
    letter-spacing: 0.2px;
  }
</style>
</head>
<body>
<div class="board">
  <svg class="board-frame" viewBox="0 0 691 1037" preserveAspectRatio="none" aria-hidden="true">
    <defs>
      <radialGradient id="sky-wash" cx="0" cy="0.45" r="0.75">
        <stop offset="0" stop-color="#5cc3ee"/>
        <stop offset="0.45" stop-color="#cee9f5"/>
        <stop offset="1" stop-color="#ffffff"/>
      </radialGradient>
      <linearGradient id="top-blue" x1="0" y1="0" x2="1" y2="0">
        <stop offset="0" stop-color="#1f3a86"/>
        <stop offset="1" stop-color="#2156a8"/>
      </linearGradient>
      <linearGradient id="silver" x1="0" y1="0" x2="1" y2="0">
        <stop offset="0" stop-color="#e8e8e8"/>
        <stop offset="0.25" stop-color="#7a7a7a"/>
        <stop offset="0.55" stop-color="#ffffff"/>
        <stop offset="0.8" stop-color="#9a9a9a"/>
        <stop offset="1" stop-color="#f2f2f2"/>
      </linearGradient>
      <linearGradient id="silver-bottom" x1="0" y1="0" x2="1" y2="0">
        <stop offset="0" stop-color="#ffffff"/>
        <stop offset="0.4" stop-color="#8a8a8a"/>
        <stop offset="0.65" stop-color="#f5f5f5"/>
        <stop offset="1" stop-color="#6f6f6f"/>
      </linearGradient>
    </defs>
    <rect width="691" height="1037" fill="url(#sky-wash)"/>
    <path d="M0 360 Q120 200 360 125 Q520 90 691 95 L691 1037 L0 1037 Z" fill="#ffffff" opacity="0.55"/>
    <path d="M0 0 H691 V78 Q400 80 180 150 Q70 185 0 205 Z" fill="url(#top-blue)"/>
    <path d="M0 205 Q70 185 180 150 Q400 80 691 78 L691 92 Q420 96 200 165 Q80 205 0 285 Z" fill="url(#silver)"/>
    <path d="M0 285 Q80 205 200 165 Q420 96 691 92 L691 110 Q430 112 220 180 Q90 225 0 355 Z" fill="#8fd2f2" opacity="0.7"/>
    <path d="M0 1037 V1006 Q300 1000 500 920 Q620 870 691 812 L691 1037 Z" fill="url(#silver-bottom)"/>
    <path d="M0 1037 V1018 Q320 1015 520 935 Q630 890 691 860 L691 1037 Z" fill="#2a4c9e"/>
    <path d="M0 1037 V1030 Q340 1030 560 960 Q640 935 691 915 L691 1037 Z" fill="#1e3c8a"/>
  </svg>

  <div class="brand">
    <div class="brand-name">TrellisWorks</div>
  </div>

  <section class="values">
    <h1 class="values-title">Our Core Values</h1>
    <p class="value"><span class="value-name plain">Integrity</span> – We believe that to be successful, it is essential to operate at the highest levels of honesty, responsibility and trust.</p>
    <p class="value"><span class="value-name">Accountability</span> – Taking responsibility for one’s own actions.</p>
    <p class="value"><span class="value-name">Respect</span> – Understand and value differences in others. Listen thoughtfully to understand.</p>
    <p class="value"><span class="value-name">Excellence</span> – We continually improve our standards and processes so that excellence simple becomes a natural consequence of our work.</p>
    <p class="value"><span class="value-name">Loyalty</span> – Working collaboratively with TrellisWorks employees, partners and customers to solve problems and achieve goals.</p>
  </section>
</div>
</body>
</html>
```